Yard sign

Looking for a yard sign. <br/>Something simple, name, number. <br/>Large text, readable from 50 feet away. <br/><br/>18 x 24 inches.

Target Market(s)

Potential homeowners thinking about going solar.

Colors

Designer to choose colors to be used in the design.

Requirements
Must have
• "WE'VE GONE SOLAR!"
Nice to have
• We are a solar company, we would like a design that compliments the homeowners decision that they went solar and encourages others to do the same.

```html
<!DOCTYPE html>
<html lang="en">
<head>
<meta charset="utf-8">
<title>Sunvale Solar Yard Sign</title>
<link rel="stylesheet" href="https://fonts.googleapis.com/css2?family=Montserrat:wght@800&family=Roboto+Condensed:wght@700;900&family=Roboto:wght@700&display=swap">
<style>
  :root {
    --backdrop: #1d1a1a;
    --sign-white: #ffffff;
    --brand-orange: #f58f23;
    --band-red: #dc4409;
    --sun-yellow: #fbc82d;
    --ink-black: #0b0b0b;
  }
  html, body {
    margin: 0;
    width: 1200px;
    height: 1200px;
    overflow: hidden;
    background: var(--backdrop);
  }
  .yard-sign {
    position: absolute;
    left: 0;
    top: 150px;
    width: 1200px;
    height: 899px;
    background: var(--sign-white);
    overflow: hidden;
  }
  .sign-bands {
    position: absolute;
    inset: 0;
  }
  .brand-mark {
    position: absolute;
    left: 170px;
    top: 130px;
    display: flex;
    align-items: center;
    gap: 26px;
  }
  .brand-dot {
    width: 210px;
    height: 210px;
    border-radius: 50%;
    background: var(--sun-yellow);
    flex: none;
  }
  .brand-text {
    display: flex;
    flex-direction: column;
  }
  .brand-name {
    margin: 0;
    font-family: "Montserrat", sans-serif;
    font-weight: 800;
    font-size: 104px;
    line-height: 0.98;
    color: var(--brand-orange);
    letter-spacing: -1px;
  }
  .slogan {
    margin: 14px 0 0;
    font-family: "Montserrat", sans-serif;
    font-weight: 800;
    font-size: 44px;
    line-height: 1;
    letter-spacing: 3px;
    color: var(--sun-yellow);
    white-space: nowrap;
  }
  .rep-name {
    position: absolute;
    left: 0;
    right: 0;
    top: 490px;
    margin: 0;
    text-align: center;
    font-family: "Roboto Condensed", sans-serif;
    font-weight: 700;
    font-size: 82px;
    letter-spacing: -2px;
    color: var(--band-red);
  }
  .phone-line {
    position: absolute;
    left: 185px;
    top: 683px;
    display: flex;
    align-items: center;
    gap: 14px;
  }
  .phone-icon {
    width: 98px;
    height: 98px;
    flex: none;
  }
  .phone-number {
    font-family: "Roboto Condensed", sans-serif;
    font-weight: 900;
    font-size: 126px;
    line-height: 1;
    color: var(--sun-yellow);
    white-space: nowrap;
  }
  .web-address {
    position: absolute;
    left: 0;
    right: 0;
    top: 795px;
    margin: 0;
    text-align: center;
    font-family: "Roboto", sans-serif;
    font-weight: 700;
    font-size: 72px;
    line-height: 1;
    color: var(--ink-black);
  }
</style>
</head>
<body>
  <main class="yard-sign">
    <svg class="sign-bands" viewBox="0 0 1200 899" width="1200" height="899" aria-hidden="true">
      <polygon points="0,538 1200,714 1200,899 0,899" fill="var(--band-red)"/>
      <polygon points="645,623 1200,543 1200,703" fill="var(--sun-yellow)"/>
    </svg>

    <div class="brand-mark">
      <span class="brand-dot"></span>
      <div class="brand-text">
        <h1 class="brand-name">SUNVALE<br>SOLAR</h1>
        <p class="slogan">WE'VE GONE SOLAR!</p>
      </div>
    </div>

    <h2 class="rep-name">MARCUS HALE</h2>

    <div class="phone-line">
      <svg class="phone-icon" viewBox="0 0 100 100" aria-hidden="true">
        <circle cx="50" cy="50" r="45" fill="none" stroke="var(--sun-yellow)" stroke-width="5"/>
        <circle cx="50" cy="50" r="39" fill="var(--band-red)"/>
        <path d="M33 27c-4 0-9 5-9 11 0 14 20 35 35 36 6 0 11-5 11-9 0-3-10-7-13-6-2 1-3 4-5 4-5-1-15-12-16-17 0-2 3-3 4-5 1-3-3-14-7-14z" fill="var(--sign-white)"/>
        <path d="M52 30a16 16 0 0 1 16 16M52 22a24 24 0 0 1 24 24M52 38a8 8 0 0 1 8 8" fill="none" stroke="var(--sign-white)" stroke-width="3" stroke-linecap="round"/>
      </svg>
      <span class="phone-number">555-014-7788</span>
    </div>

    <p class="web-address">www.sunvale.net</p>
  </main>
</body>
</html>
```